Payday Lending App Interface Design

Hello, we are building a payday lending application, Lendoro, that lend people money. I have drafted some of the screens that show the functionalities we have at the moment, please find the screens in attachments.
The elements in the screens are placed just to show what should be included in those screens, it's not necessary to follow the same layout. If you have better design ideas, you are very welcomed to show off your talent.
I think what we want is a style guide so that we can apply the same style to any screens that are similar to the ones I attached. We really like
the style as in the attached image called Style.png. We might want something similar - a simple, clean design yet fun and engaging. Customised graphical elements such as icons, illustrations are preferable.
Apart from the attached screens, we might also need a design for the On Board screen and the Login/Sign Up screen too.
Our logo colour is in yellow and black. Perhaps we will have a similar colour theme. I also attached the logo file, icon-Lendoro.png, if you would like to put it in your design.
Please message me if you need further information.
Regards
Target Market(s)
Young people that doesn't have strong income

```html
<!DOCTYPE html>
<html lang="en">
<head>
<meta charset="utf-8">
<title>Lendoro – App Screens</title>
<link href="https://fonts.googleapis.com/css2?family=Montserrat:wght@400;500;700;800&display=swap" rel="stylesheet">
<style>
  :root {
    --yellow: #f9d40b;
    --yellow-deep: #d9b300;
    --cream: #fbf3c8;
    --ink: #050505;
    --field-border: #b9b5a4;
    --text: #1d1d1d;
    --bg-top: #444444;
    --bg-bottom: #6b6b6b;
  }
  * { box-sizing: border-box; margin: 0; padding: 0; }
  html, body { width: 1200px; height: 2515px; overflow: hidden; }
  body {
    position: relative;
    font-family: "Montserrat", sans-serif;
    color: var(--ink);
    background: linear-gradient(180deg, var(--bg-bottom) 0%, var(--bg-top) 30%, var(--bg-top) 60%, var(--bg-bottom) 100%);
  }
  .backdrop-wave { position: absolute; left: 0; top: 0; width: 1200px; height: 2515px; }

  .screen { position: absolute; width: 449px; overflow: hidden; background: var(--cream); }
  .screen--welcome { left: 146px; top: 156px; height: 967px; background: var(--yellow); border-radius: 34px; }
  .screen--details { left: 659px; top: 129px; height: 1102px; }
  .screen--settings { left: 153px; top: 1195px; height: 1102px; }
  .screen--bank { left: 659px; top: 1285px; height: 1102px; }

  .header-curve { position: absolute; left: 0; top: 0; width: 449px; height: 200px; }

  .brand-tile {
    position: absolute; left: 137px; width: 174px; height: 174px;
    background: var(--yellow); border-radius: 30px;
    box-shadow: 0 5px 8px rgba(0,0,0,0.25);
    display: flex; align-items: center; justify-content: center;
    font-weight: 800; font-size: 32px; color: var(--ink);
  }
  .screen--welcome .brand-tile { left: 102px; top: 36px; width: 245px; height: 240px; font-size: 44px; border-radius: 40px; box-shadow: 0 4px 8px rgba(0,0,0,0.18); }

  .welcome-title { position: absolute; left: 0; width: 100%; top: 325px; text-align: center; font-weight: 800; font-size: 47px; line-height: 57px; }
  .welcome-copy { position: absolute; left: 0; width: 100%; top: 472px; text-align: center; font-size: 22px; line-height: 45px; font-weight: 400; }
  .photo { position: absolute; left: 0; }
  .welcome-photo { top: 640px; width: 449px; height: 327px; background: linear-gradient(180deg, rgba(249,212,11,0) 0%, #b9a020 35%, #6d6a1e 75%, #3b3a10 100%); }

  .pill {
    position: absolute; display: flex; align-items: center; justify-content: center;
    border-radius: 40px; font-weight: 800; letter-spacing: 0.5px;
  }
  .pill--dark { background: var(--ink); color: var(--yellow); left: 76px; top: 634px; width: 297px; height: 84px; font-size: 27px; }
  .pill--yellow { background: var(--yellow); color: var(--ink); }

  .screen-title { position: absolute; left: 0; width: 100%; text-align: center; font-weight: 800; font-size: 49px; }
  .screen-sub { position: absolute; left: 0; width: 100%; text-align: center; font-size: 23px; line-height: 40px; }

  .field {
    position: absolute; background: #fff; border: 1.5px solid var(--field-border);
    border-radius: 4px; display: flex; align-items: center; padding-left: 36px;
    font-size: 22px; color: var(--text);
  }
  .details-photo { top: 700px; width: 449px; height: 402px; background: linear-gradient(180deg, rgba(251,243,200,0) 0%, #e8dfb2 45%, #d6cba0 100%); }

  .card { position: absolute; background: #fff; border: 1.5px solid #cfcab4; }
  .card-rule { position: absolute; height: 5px; background: var(--yellow); }
  .close-btn { position: absolute; width: 62px; height: 62px; border-radius: 50%; background: var(--yellow); display: flex; align-items: center; justify-content: center; }
  .settings-photo { top: 480px; width: 449px; height: 622px; background: linear-gradient(180deg, rgba(251,243,200,0) 0%, #c9c29c 45%, #55534a 75%, #2d2d2a 100%); }
  .bank-photo { top: 620px; width: 449px; height: 482px; background: linear-gradient(180deg, rgba(251,243,200,0) 0%, #d9d1a8 50%, #a39c7c 80%, #7d7862 100%); }

  .bank-name { position: absolute; display: flex; align-items: center; gap: 14px; font-weight: 700; font-size: 30px; color: var(--ink); }
  .bank-name .mark { width: 40px; height: 40px; background: #d2151d; }
</style>
</head>
<body>
  <svg class="backdrop-wave" viewBox="0 0 1200 2515" aria-hidden="true">
    <defs>
      <linearGradient id="waveFill" x1="0" y1="0" x2="0" y2="1">
        <stop offset="0" stop-color="#f5ca00"/>
        <stop offset="1" stop-color="#b89a05"/>
      </linearGradient>
    </defs>
    <path d="M0 2205 Q560 2150 1200 2232 L1200 2515 L0 2515 Z" fill="url(#waveFill)"/>
  </svg>

  <!-- Welcome screen -->
  <section class="screen screen--welcome">
    <div class="brand-tile">Lendoro</div>
    <h1 class="welcome-title">Connecting to<br>your Bank</h1>
    <p class="welcome-copy">Please don't exit the app.It takes<br>3-5 minutes to confirm your<br>details with your bank.</p>
    <div class="photo welcome-photo" role="img" aria-label="Photo of two smiling young people shaking hands across a table"></div>
    <div class="pill pill--dark">GET STARTED</div>
  </section>

  <!-- Personal details screen -->
  <section class="screen screen--details">
    <div class="photo details-photo" role="img" aria-label="Photo of a pen resting on a paper application form"></div>
    <svg class="header-curve" viewBox="0 0 449 200" aria-hidden="true">
      <path d="M0 112 Q224 250 449 112 L449 0 L0 0 Z" fill="var(--yellow)"/>
      <path d="M0 100 Q224 236 449 100 L449 0 L0 0 Z" fill="var(--ink)"/>
    </svg>
    <div class="brand-tile" style="top:51px">Lendoro</div>
    <h2 class="screen-title" style="top:262px">Personal Details</h2>
    <p class="screen-sub" style="top:342px">Please provide details as<br>shown on ID</p>
    <div class="field" style="left:27px;top:454px;width:394px;height:95px">Given Name</div>
    <div class="field" style="left:27px;top:563px;width:394px;height:95px">Middle Name</div>
    <div class="field" style="left:27px;top:671px;width:394px;height:95px">Surname</div>
    <div class="field" style="left:27px;top:780px;width:394px;height:95px">Date of Birth(DD/MM/YY)</div>
    <div class="pill pill--yellow" style="left:27px;top:961px;width:394px;height:78px;font-size:36px">NEXT</div>
  </section>

  <!-- Settings screen -->
  <section class="screen screen--settings">
    <div class="photo settings-photo" role="img" aria-label="Photo of a hand using a calculator beside a laptop"></div>
    <svg class="header-curve" viewBox="0 0 449 200" aria-hidden="true">
      <path d="M0 112 Q224 250 449 112 L449 0 L0 0 Z" fill="var(--yellow)"/>
      <path d="M0 100 Q224 236 449 100 L449 0 L0 0 Z" fill="var(--ink)"/>
    </svg>
    <div class="brand-tile" style="top:51px">Lendoro</div>
    <div class="card" style="left:28px;top:276px;width:394px;height:610px"></div>
    <div class="close-btn" style="left:364px;top:271px">
      <svg width="22" height="22" viewBox="0 0 22 22" aria-hidden="true"><path d="M3 3 L19 19 M19 3 L3 19" stroke="var(--ink)" stroke-width="4.5" stroke-linecap="round"/></svg>
    </div>
    <h2 class="screen-title" style="top:321px;font-size:50px">Settings</h2>
    <div class="card-rule" style="left:23px;top:426px;width:405px"></div>
    <div class="field" style="left:49px;top:459px;width:352px;height:84px;font-size:19px;padding-left:33px">Personal Details</div>
    <div class="field" style="left:49px;top:556px;width:352px;height:84px;font-size:19px;padding-left:33px">Bank Accounts</div>
    <div class="field" style="left:49px;top:652px;width:352px;height:84px;font-size:19px;padding-left:33px">Account Settings</div>
    <div class="pill pill--yellow" style="left:51px;top:774px;width:349px;height:74px;font-size:29px">LOG OUT</div>
  </section>

  <!-- Connect bank screen -->
  <section class="screen screen--bank">
    <div class="photo bank-photo" role="img" aria-label="Photo of a classical bank building facade with columns"></div>
    <svg class="header-curve" viewBox="0 0 449 200" aria-hidden="true">
      <path d="M0 112 Q224 250 449 112 L449 0 L0 0 Z" fill="var(--yellow)"/>
      <path d="M0 100 Q224 236 449 100 L449 0 L0 0 Z" fill="var(--ink)"/>
    </svg>
    <div class="brand-tile" style="top:50px">Lendoro</div>
    <div class="card" style="left:27px;top:274px;width:394px;height:611px"></div>
    <svg style="position:absolute;left:40px;top:288px" width="46" height="46" viewBox="0 0 46 46" aria-hidden="true">
      <circle cx="23" cy="23" r="20" fill="none" stroke="var(--ink)" stroke-width="3"/>
      <path d="M33 23 H14 M22 15 L14 23 L22 31" fill="none" stroke="var(--ink)" stroke-width="3.5" stroke-linecap="round" stroke-linejoin="round"/>
    </svg>
    <h2 class="screen-title" style="top:318px;font-size:48px;line-height:57px">Connect<br>Your Bank</h2>
    <div class="card-rule" style="left:22px;top:452px;width:405px"></div>
    <div class="bank-name" style="left:52px;top:482px"><span class="mark"></span>Northgate</div>
    <div class="field" style="left:49px;top:553px;width:351px;height:84px;font-size:20px;padding-left:33px">Account Number</div>
    <div class="field" style="left:49px;top:650px;width:351px;height:84px;font-size:20px;padding-left:33px">Password</div>
    <div class="pill pill--yellow" style="left:50px;top:775px;width:350px;height:74px;font-size:29px">CONNECT</div>
  </section>
</body>
</html>
```